Business card design Needed for new logo / Construction business, home extensions and new builds

We need a business card design using our new logo files which i will attach to this project :)

We are a small construction business specialising in home extensions, new builds and property development. We are very ambitious and would appreciate professional and elegant designs for our new business card.

Very serious about using the services on MakerQuarry and recently acquired our new logo from here :)

Please get involved, i will feedback when i can as i am very busy but can respond daily, thanks

Target Market(s)

People that want to build onto their houses, new building developments or adding too their existing property

Industry/Entity Type

Construction

Contact Information for Business Card

Renwick Tolliver Construction, Lionel Ashby (Managing Director), Tel 07822254961, email - info@renwick-tolliver, www.renwick-tolliver.co.uk

Colors

Designer to choose colors to be used in the design.

Requirements
Must have
• I like a deep grey on the back please. A lot of you have provided black from and back, try mixing things up a little. The black looks cool 😎 Thanks

```html
<!DOCTYPE html>
<html lang="en">
<head>
<meta charset="utf-8">
<title>Renwick Tolliver Construction — Business Card</title>
<link href="https://fonts.googleapis.com/css2?family=Cinzel:wght@500;600&family=Poppins:wght@300;400&display=swap" rel="stylesheet">
<style>
  :root {
    --backdrop: #2b2422;
    --card-back: #1c1c1c;
    --card-front: #131313;
    --gold-dark: #a8731a;
    --gold-light: #f4d27c;
    --gold-mid: #c9962e;
    --silver: #d9dadc;
    --silver-dark: #8c8e92;
    --text-light: #e9e9e9;
    --text-muted: #a9a9a9;
    --gold-gradient: linear-gradient(90deg, var(--gold-dark), var(--gold-light) 50%, var(--gold-mid));
  }
  * { margin: 0; padding: 0; box-sizing: border-box; }
  html, body { width: 1200px; height: 842px; overflow: hidden; }
  body {
    background: var(--backdrop);
    display: flex;
    align-items: center;
    justify-content: center;
    gap: 48px;
    font-family: "Poppins", sans-serif;
  }
  .card {
    position: relative;
    width: 530px;
    height: 303px;
    overflow: hidden;
    box-shadow: 0 14px 30px rgba(0,0,0,.45);
  }

  /* Contact side */
  .card--contact { background: var(--card-back); }
  .gold-band {
    position: absolute; left: 0; right: 0; height: 15px;
    background: var(--gold-gradient);
  }
  .gold-band--top { top: 0; }
  .gold-band--bottom { bottom: 0; }
  .contact {
    position: absolute; left: 0; right: 0; top: 62px;
    text-align: center;
  }
  .contact__name {
    font-family: "Cinzel", serif; font-weight: 600;
    font-size: 25px; letter-spacing: .5px;
    color: var(--gold-mid);
    line-height: 1;
  }
  .contact__role {
    font-size: 12px; font-weight: 300; letter-spacing: .6px;
    color: var(--text-muted); text-transform: uppercase;
    margin-top: 4px;
  }
  .divider {
    width: 46px; height: 1.5px; margin: 12px auto;
    background: var(--gold-gradient);
  }
  .contact__line {
    font-size: 13px; font-weight: 300; color: var(--text-light);
    text-transform: uppercase; line-height: 1.35; letter-spacing: .3px;
  }
  .contact__line--phone { font-size: 15px; font-weight: 400; }
  .contact__address {
    font-size: 12.5px; font-weight: 300; color: var(--text-muted);
    text-transform: uppercase; line-height: 1.4; letter-spacing: .3px;
    margin-top: 20px;
  }

  /* Brand side */
  .card--brand { background: var(--card-front); }
  .edge-tab {
    position: absolute; width: 48px; height: 54px;
    display: flex; align-items: stretch;
  }
  .edge-tab__gold { flex: 1; background: var(--gold-gradient); }
  .edge-tab__silver {
    width: 4px; margin: 0 6px;
    background: linear-gradient(180deg, var(--silver-dark), var(--silver), var(--silver-dark));
  }
  .edge-tab--left { left: 0; top: 156px; }
  .edge-tab--right { right: 0; top: 58px; flex-direction: row-reverse; }
  .brand {
    position: absolute; left: 90px; right: 40px; top: 0; bottom: 0;
    display: flex; flex-direction: column; align-items: center; justify-content: center;
    text-align: center;
  }
  .brand__mark {
    width: 16px; height: 16px; background: var(--gold-mid); margin-bottom: 16px;
  }
  .brand__name {
    font-family: "Cinzel", serif; font-weight: 500;
    font-size: 27px; letter-spacing: 1px; line-height: 1.25;
    color: var(--gold-mid);
  }
</style>
</head>
<body>
  <section class="card card--contact" aria-label="Contact side">
    <div class="gold-band gold-band--top"></div>
    <div class="contact">
      <p class="contact__name">Lionel Ashby</p>
      <p class="contact__role">Managing Director</p>
      <div class="divider"></div>
      <p class="contact__line contact__line--phone">07822254961</p>
      <p class="contact__line">info@renwick-tolliver</p>
      <p class="contact__line">www.renwick-tolliver.co.uk</p>
      <div class="divider"></div>
      <p class="contact__address">421, Address line goes here<br>45452, Country name</p>
    </div>
    <div class="gold-band gold-band--bottom"></div>
  </section>

  <section class="card card--brand" aria-label="Brand side">
    <div class="edge-tab edge-tab--left"><span class="edge-tab__gold"></span><span class="edge-tab__silver"></span></div>
    <div class="edge-tab edge-tab--right"><span class="edge-tab__gold"></span><span class="edge-tab__silver"></span></div>
    <div class="brand">
      <span class="brand__mark"></span>
      <p class="brand__name">Renwick Tolliver<br>Construction</p>
    </div>
  </section>
</body>
</html>
```